Business card for my new company (Accounting firm)

I need a business card for my new business Brightwell Advisory and Ledger SA. Our services are accounting, tax, audit and financial management. Our customers are small companies, start-ups and new companies. The final design has to show financial security, trust and growth. Please find our logo attached to the business card. Text for the business card: Brightwell Advisory and Ledger SA Tomas Varenholt Director and Founder Certified Accountant Tel. 022 418 57 34 tv@clairevalconseil.ch www.clairevalconseil.ch Rue des Vergières 27 1201 Geneva
Target Market(s)
Our customers are small companies, start-ups and new companies.
Industry/Entity Type
Finance And Accounting
Contact Information for Business Card
Claireval Conseil et Comptes SA
Tomas Varenholt
Directeur et Fondateur
Expert-comptable diplômé
Tél. 022 418 57 34
tv@clairevalconseil.ch
www.clairevalconseil.ch
Rue des Vergières 27
1201 Genève

```html
<!DOCTYPE html>
<html lang="fr">
<head>
<meta charset="utf-8">
<title>Claireval Conseil et Comptes SA – Carte de visite</title>
<link rel="stylesheet" href="https://fonts.googleapis.com/css2?family=Roboto:wght@400;500;700&display=swap">
<style>
  :root {
    --backdrop: #3b3c3f;
    --card: #1e1f22;
    --blue: #2b9fdc;
    --blue-deep: #1a6fa6;
    --white: #f4f6f8;
    --emboss: #3a3b3f;
  }
  * { box-sizing: border-box; margin: 0; padding: 0; }
  html, body {
    width: 799px; height: 1200px; overflow: hidden;
    background: var(--backdrop);
    font-family: "Roboto", Arial, sans-serif;
  }
  .sheet { position: relative; width: 799px; height: 1200px; }
  .card {
    position: absolute; left: 90px; width: 620px; height: 360px;
    background: var(--card); overflow: hidden;
    box-shadow: 0 18px 40px rgba(0,0,0,.45);
  }
  .card--front { top: 150px; }
  .card--back { top: 660px; }

  /* front */
  .front-band { position: absolute; left: 0; right: 0; bottom: 0; height: 14px; background: var(--blue); }
  .wordmark { position: absolute; display: flex; align-items: center; gap: 18px; }
  .wordmark__mark { width: 46px; height: 46px; flex: none; }
  .wordmark__name { font-weight: 500; line-height: 1; text-transform: uppercase; }
  .wordmark__main { display: block; font-size: 46px; letter-spacing: 7px; }
  .wordmark__sub { display: block; font-size: 13px; letter-spacing: 4.2px; margin-top: 8px; }
  .card--front .wordmark { left: 50%; top: 50%; transform: translate(-50%, -55%); }
  .card--front .wordmark__mark { background: var(--emboss); }
  .card--front .wordmark__name { color: var(--emboss); }

  /* back */
  .card--back .wordmark { left: 150px; top: 46px; }
  .card--back .wordmark__mark { background: var(--blue); }
  .card--back .wordmark__name { color: var(--white); }
  .wordmark--small .wordmark__main { font-size: 38px; letter-spacing: 6px; }
  .wordmark--small .wordmark__sub { font-size: 11px; letter-spacing: 3.4px; }

  .holder { position: absolute; left: 40px; top: 146px; }
  .holder__name { color: var(--blue); font-weight: 700; font-size: 25px; margin-bottom: 8px; }
  .holder__role { color: var(--white); font-size: 14px; line-height: 1.35; }

  .contact { position: absolute; left: 372px; top: 180px; list-style: none; }
  .contact__item { display: flex; align-items: center; gap: 12px; color: var(--white); font-size: 15px; height: 24px; }
  .contact__icon { width: 14px; height: 14px; fill: var(--blue); flex: none; }

  .back-bands { position: absolute; left: 0; bottom: 0; width: 620px; height: 100px; }
  .address { position: absolute; right: 30px; bottom: 24px; color: var(--white); font-size: 16px; }
</style>
</head>
<body>
<main class="sheet">
  <section class="card card--front" aria-label="Recto">
    <div class="wordmark">
      <span class="wordmark__mark"></span>
      <span class="wordmark__name">
        <span class="wordmark__main">Claireval</span>
        <span class="wordmark__sub">Conseil et Comptes SA</span>
      </span>
    </div>
    <div class="front-band"></div>
  </section>

  <section class="card card--back" aria-label="Verso">
    <div class="wordmark wordmark--small">
      <span class="wordmark__mark"></span>
      <span class="wordmark__name">
        <span class="wordmark__main">Claireval</span>
        <span class="wordmark__sub">Conseil et Comptes SA</span>
      </span>
    </div>

    <div class="holder">
      <p class="holder__name">Tomas Varenholt</p>
      <p class="holder__role">Directeur et Fondateur</p>
      <p class="holder__role">Expert-comptable diplômé</p>
    </div>

    <ul class="contact">
      <li class="contact__item">
        <svg class="contact__icon" viewBox="0 0 16 16"><path d="M3 1h3l1.5 4-2 1.3a9 9 0 0 0 4.2 4.2L11 8.5l4 1.5v3a2 2 0 0 1-2 2A13 13 0 0 1 1 3a2 2 0 0 1 2-2z"/></svg>
        <span>022 418 57 34</span>
      </li>
      <li class="contact__item">
        <svg class="contact__icon" viewBox="0 0 16 16"><path d="M1 3h14v10H1z M1 3l7 6 7-6" stroke="#1e1f22" stroke-width="1.2"/></svg>
        <span>tv@clairevalconseil.ch</span>
      </li>
      <li class="contact__item">
        <svg class="contact__icon" viewBox="0 0 16 16"><circle cx="8" cy="8" r="7"/><path d="M1 8h14M8 1c-3 4-3 10 0 14M8 1c3 4 3 10 0 14" stroke="#1e1f22" stroke-width="1" fill="none"/></svg>
        <span>www.clairevalconseil.ch</span>
      </li>
    </ul>

    <svg class="back-bands" viewBox="0 0 620 100" aria-hidden="true">
      <defs>
        <linearGradient id="tab-fill" x1="0" x2="1">
          <stop offset="0" stop-color="#1a6fa6"/>
          <stop offset="1" stop-color="#2b9fdc"/>
        </linearGradient>
      </defs>
      <rect x="0" y="32" width="310" height="12" fill="#2b9fdc"/>
      <path d="M290 44 L310 32 L334 16 H620 V100 H290 Z" fill="url(#tab-fill)"/>
    </svg>
    <p class="address">Rue des Vergières 27 1201 Genève</p>
  </section>
</main>
</body>
</html>
```